Summit Bodyform Gym Website

We need a website design for our gym.

Summit is the UAE's first calisthenics and parkour gym. The theme under which the gym revolves is that one does not require any machinery to workout as our bodies could be themselves the machinery. The gym is designed to be the more of a social hub rather than an "in-and-out" gym, where people come train, have fun, hang out and socialize for a few hours rather than just train for 60 minutes then leave. The gym is designed to be a big open space with lots of natural sunlight, natural wood and plants all over the place to create a natural and refreshing setting. We also use recycled material throughout the gym and recycle our waste as being green is part of our philosophy. We currently also have some of the world's top and most recognized calisthenics athletes working with us.

We would like our website to reflect all that as well as provide a simple, interactive and fun way for visitors to be able to get class and gym information, check out gym media and contact us for bookings.

Target Market(s)

Ages 15-35

Industry/Entity Type

Fitness

Coding

Coded - Design and coding required

Number of Pages Required

4 page

Font styles to use
Decorative

Colors
0792cd

Requirements
Must have
• Class descriptions
• Gym description
• Class schedules
• Trainer profiles
• Gym philosophy
• Contact Details
Nice to have
• A link to contact us directly for a free first trial class

```html
<!DOCTYPE html>
<html lang="en">
<head>
<meta charset="utf-8">
<title>Summit Bodyform Gym</title>
<link href="https://fonts.googleapis.com/css2?family=Anton&family=Armata&family=Open+Sans:wght@400;700&display=swap" rel="stylesheet">
<style>
:root{
  --brand:#0792cd;
  --brand-deep:#0a86ba;
  --ink:#1f1f1f;
  --dark:#242424;
  --nav:#262626;
  --page:#eeeeee;
  --white:#ffffff;
  --muted:#4a4a4a;
  --foot-text:#bdbdbd;
}
*{margin:0;padding:0;box-sizing:border-box}
html,body{width:746px;height:1200px;overflow:hidden}
body{position:relative;background:var(--page);font-family:"Armata",sans-serif;color:var(--ink)}
.hero{position:absolute;left:0;top:0;width:746px;height:485px;
  background:linear-gradient(180deg,#5a5654 0%,#7b5a3f 25%,#6b5a48 45%,#4a3a34 62%,#6d3d34 80%,#5b3630 100%)}
.hero-title{position:absolute;left:0;width:746px;text-align:center;color:var(--white);font-family:"Anton",sans-serif;text-shadow:0 2px 4px rgba(0,0,0,.35)}
.hero-title.main{top:192px;font-size:46px;letter-spacing:.2px}
.hero-title.sub{top:253px;font-size:28px}
.topbar{position:absolute;left:175px;top:21px;width:571px;height:31px;background:var(--brand)}
.phone{position:absolute;left:296px;top:6px;display:flex;align-items:center;gap:8px;color:var(--white);font-family:"Open Sans",sans-serif;font-size:14px}
.socials{position:absolute;left:427px;top:8px;display:flex;gap:10px}
.socials span{width:16px;height:16px;border-radius:50%;background:var(--white)}
.navbar{position:absolute;left:175px;top:52px;width:571px;height:30px;background:var(--nav);display:flex;align-items:center;padding-left:28px;gap:29px}
.navbar a{color:var(--white);text-decoration:none;font-family:"Open Sans",sans-serif;font-weight:700;font-size:8.5px}
.navstrip{position:absolute;left:175px;top:82px;width:571px;height:15px;background:var(--brand)}
.brand-box{position:absolute;left:0;top:21px;width:175px;height:76px;background:var(--white);display:flex;align-items:center;justify-content:center;gap:7px}
.brand-dot{width:10px;height:10px;border-radius:50%;background:var(--brand)}
.brand-name{font-size:13px;color:var(--ink);line-height:1.15}
.tabs{position:absolute;left:49px;top:390px;width:648px;height:95px;display:flex;background:var(--brand)}
.tab{width:129.6px;position:relative;text-align:center;color:var(--white);border-right:1px solid rgba(0,0,0,.12)}
.tab:last-child{border-right:none}
.tab .icon{position:absolute;left:50%;top:11px;transform:translateX(-50%);width:52px;height:52px;border-radius:50%;background:var(--white);display:flex;align-items:center;justify-content:center}
.tab .label{position:absolute;left:0;right:0;top:67px;font-size:13.5px}
.tab.active{background:var(--dark);margin-top:-26px;height:121px}
.tab.active .icon{top:9px;width:68px;height:68px;border:4px solid var(--brand)}
.tab.active .label{top:81px;font-size:15px}
.watermark{position:absolute;left:410px;top:478px;font-size:56px;color:rgba(0,0,0,.045);line-height:1;white-space:nowrap}
.watermark small{display:block;font-size:20px;margin-top:6px;margin-left:100px}
.section-title{position:absolute;left:37px;top:537px;height:39px;border-left:5px solid var(--ink);padding-left:10px;font-size:24px;line-height:39px}
.section-title em{font-style:normal;color:var(--brand)}
.card{position:absolute;top:621px;width:206px;height:329px;background:var(--white);text-align:center}
.card .photo{width:206px;height:137px}
.card h3{font-weight:400;font-size:17.5px;margin-top:18px}
.card .rule{width:50px;height:2px;background:var(--brand);margin:7px auto 10px}
.card p{font-family:"Open Sans",sans-serif;font-size:9px;line-height:12.8px;color:var(--muted);padding:0 14px}
.card .btn{display:inline-block;margin-top:16px;width:87px;height:26px;border:2px solid var(--ink);font-family:"Open Sans",sans-serif;font-size:9px;line-height:22px;color:var(--ink)}
.footer{position:absolute;left:0;top:1003px;width:746px;height:197px;background:var(--dark);text-align:center;color:var(--foot-text)}
.footer .brand{display:flex;justify-content:center;align-items:center;gap:7px;margin-top:38px;color:var(--white);font-size:15px}
.footer address{font-style:normal;font-size:11px;line-height:17.5px;margin-top:28px}
.footer .rule{width:350px;height:1px;background:#3a3a3a;margin:13px auto 0}
.footer .copy{font-size:9px;margin-top:10px}
</style>
</head>
<body>
<div class="hero" role="img" aria-label="Gym interior with wooden wall, plant lettering, racks, dumbbells and exercise balls"></div>
<h1 class="hero-title main">Summit is the UAE's first</h1>
<p class="hero-title sub">calisthenics and parkour gym</p>

<div class="brand-box"><span class="brand-dot"></span><span class="brand-name">Summit<br>Bodyform Gym</span></div>
<div class="topbar">
  <div class="phone">
    <svg width="14" height="14" viewBox="0 0 24 24"><path d="M6 2l4 4-2 3c1 3 4 6 7 7l3-2 4 4-3 4C10 21 3 14 2 5z" fill="none" stroke="#fff" stroke-width="2"/></svg>
    1300 555 018
  </div>
  <div class="socials"><span></span><span></span><span></span><span></span></div>
</div>
<nav class="navbar">
  <a href="#">HOME</a><a href="#">ABOUT US</a><a href="#">CLASSES</a><a href="#">TRAINERS</a><a href="#">EVENT</a><a href="#">ELEMENTS</a><a href="#">SHOP</a><a href="#">CONTACT</a>
</nav>
<div class="navstrip"></div>

<div class="tabs">
  <div class="tab"><div class="icon"><svg width="28" height="28" viewBox="0 0 28 28" fill="none" stroke="#222" stroke-width="2"><rect x="2" y="3" width="16" height="12"/><circle cx="21" cy="13" r="3" fill="#222"/><path d="M16 19h9v7M19 19v7"/></svg></div><div class="label">Class Description</div></div>
  <div class="tab active"><div class="icon"><svg width="34" height="30" viewBox="0 0 34 30" fill="#222"><rect x="2" y="5" width="30" height="3"/><rect x="3" y="1" width="4" height="11"/><rect x="27" y="1" width="4" height="11"/><circle cx="17" cy="14" r="3"/><rect x="11" y="18" width="12" height="6"/><rect x="10" y="26" width="14" height="3"/></svg></div><div class="label">Gym Description</div></div>
  <div class="tab"><div class="icon"><svg width="30" height="28" viewBox="0 0 30 28" fill="none" stroke="#222" stroke-width="2"><rect x="2" y="3" width="24" height="20"/><path d="M2 8h24M7 12h3M12 12h3M17 12h3M7 16h3M12 16h3"/><circle cx="23" cy="21" r="5" fill="#fff"/></svg></div><div class="label">Class Schedules</div></div>
  <div class="tab"><div class="icon"><svg width="32" height="28" viewBox="0 0 32 28" fill="#222"><rect x="4" y="3" width="3" height="18"/><rect x="4" y="3" width="8" height="3"/><rect x="4" y="19" width="26" height="5" rx="2"/></svg></div><div class="label">Trainer Profiles</div></div>
  <div class="tab"><div class="icon"><svg width="30" height="30" viewBox="0 0 30 30" fill="none" stroke="#222" stroke-width="2"><circle cx="12" cy="17" r="6"/><path d="M12 17l8-10h4M18 11v6M6 26h20"/></svg></div><div class="label">Gym Philosophy</div></div>
</div>

<div class="watermark" aria-hidden="true">summit.<small>bodyform gym</small></div>
<h2 class="section-title">Gym <em>Description</em></h2>

<article class="card" style="left:37px">
  <div class="photo" role="img" aria-label="Gymnastic ring hanging from a blue rig" style="background:linear-gradient(135deg,#3a5a86,#1d3f7a 55%,#262a30)"></div>
  <h3>Calisthenics Gym</h3><div class="rule"></div>
  <p>Curabitur fermentum odio ac enim inter-dum consequat. Sed vel faucibus leo. Ut turpis ipsum, fringilla eget vel faucibus leo. Ut turpis ipsum, fringilla tortor in, placerat rhoncus nibh. ...</p>
  <a class="btn">Read More</a>
</article>
<article class="card" style="left:271px">
  <div class="photo" role="img" aria-label="Open training floor with calisthenics frame" style="background:linear-gradient(180deg,#d9d9d9,#8d8d8d 50%,#2e2e2e)"></div>
  <h3>Calisthenics Gym</h3><div class="rule"></div>
  <p>Curabitur fermentum odio ac enim inter-dum consequat. Sed vel faucibus leo. Ut turpis ipsum, fringilla eget vel faucibus leo. Ut turpis ipsum, fringilla tortor in, placerat rhoncus nibh. ...</p>
  <a class="btn">Read More</a>
</article>
<article class="card" style="left:504px">
  <div class="photo" role="img" aria-label="Athlete training on a blue bar rig" style="background:linear-gradient(135deg,#2a3a4a,#3f6a9a 50%,#1f4fa0)"></div>
  <h3>Calisthenics Gym</h3><div class="rule"></div>
  <p>Curabitur fermentum odio ac enim inter-dum consequat. Sed vel faucibus leo. Ut turpis ipsum, fringilla eget vel faucibus leo. Ut turpis ipsum, fringilla tortor in, placerat rhoncus nibh. ...</p>
  <a class="btn">Read More</a>
</article>

<footer class="footer">
  <div class="brand"><span class="brand-dot"></span>Summit Bodyform Gym</div>
  <address>48 Cedar Point, Harbour Road, Suite 310, UAE<br>800 555 0142 – hello@summitbodyform.example</address>
  <div class="rule"></div>
  <p class="copy">Copyright © 2015 – Summit Bodyform Gym – All rights reserved.</p>
</footer>
</body>
</html>
```